Restaurant Menu New Design

Hello Designers,

Blue Fern is a casual family oriented dine-in restaurant, we serve American Italian dishes like Pizza, Pasta, and Sandwiches.

We are excited about adding some new delicious dishes and recipes to our menu. And we are looking for a talented and creative designer to design it.

The menu is a 12 page black leather book, page size is:
6.5" X 11.69" (16.51 cm X 29.69 cm)

Below is the scope of work and requirements:

1) Design a completely all new, creative, and beautiful menu, including cover page, blue fern oven intro. page, interior pages, and kids menu page.

2) Design a take out edition of the menu. It will be exactly the same as the dine-in menu, but with the addition of a back cover page with info such as contacts, social media, location map, etc…

3) Files are required in Adobe Illustrator format. Layers should be organized, all text should be editable, and all the food pictures easy to change.

4) This is a two language menu, so you are required to make space in the design for a second language. The easiest way to do that is have every item listed in English twice, then I will edit the second text with Illustrator.

5) In your initial design submission, the minimum you are required to submit are these 4 pages:
– Cover page
– Typical interior menu page
– Kids menu page
– Take-out menu back cover page

If your initial design is selected, then you are required to submit all remaining pages to complete the project.

In the link below, you will find:
1) Logo
2) New menu text in Excel
3) Food images (will take some time to upload)
4) The old dine-in and take out menu designs

https://www.filevaultra.com/sh/kq7tmwzabe3pxd/BBBrTnpLk41QaWmZpQ8V2X7Jd?dl=0

Thank you for stopping by and reading this brief. I hope you like this project and enjoy designing our new menu. Please let me know if you have any questions.

Cheers!

Project Deadline Extended
Reason: We have decided to extend the deadline due to the low number of submissions which was much lower than the expected submissions we were give by Brief Harbor.

```html
<!DOCTYPE html>
<html lang="en">
<head>
<meta charset="utf-8">
<title>Main Course Menu</title>
<link rel="stylesheet" href="https://fonts.googleapis.com/css2?family=Lato:wght@400;700;900&family=Noto+Kufi+Arabic:wght@400;600&display=swap">
<style>
  :root {
    --board: #333335;
    --chalk: #ffffff;
    --muted: #9c9c9e;
    --muted-ar: #b4b4b6;
    --line: #d9d9d9;
    --icon-fill: #46464a;
    --icon-line: #bdbdbd;
    --photo-a: #c9b9a2;
    --photo-b: #8e6a45;
    --plate: #f4f1ec;
  }
  * { margin: 0; padding: 0; box-sizing: border-box; }
  html, body { width: 1200px; height: 2174px; overflow: hidden; background: var(--board); }
  .menu-page {
    position: relative; width: 1200px; height: 2174px;
    background: var(--board); color: var(--chalk);
    font-family: "Lato", Arial, sans-serif;
  }
  .rules { position: absolute; inset: 0; pointer-events: none; }
  .heading {
    position: absolute; top: 64px; font-size: 40px; font-weight: 400;
    letter-spacing: 1px; transform: translateX(-50%);
  }
  .heading--left { left: 317px; }
  .heading--right { left: 875px; }
  .doodle {
    position: absolute; background: var(--icon-fill); border-radius: 50%;
    border: 2px solid var(--icon-line);
  }
  .doodle-row {
    position: absolute; background: var(--icon-fill); border-radius: 20px;
    border: 2px solid var(--icon-line);
  }
  .photo {
    position: absolute; top: 258px; width: 430px; height: 287px;
    background: radial-gradient(ellipse at 50% 55%, var(--plate) 0 38%, transparent 39%),
                linear-gradient(135deg, var(--photo-a), var(--photo-b));
  }
  .photo--left { left: 106px; }
  .photo--right { left: 671px; }
  .dish {
    position: absolute; width: 380px; text-align: center; transform: translateX(-50%);
  }
  .dish--left { left: 319px; }
  .dish--right { left: 877px; }
  .dish__name {
    font-size: 25px; font-weight: 700; line-height: 31px; color: var(--chalk);
    text-transform: uppercase;
  }
  .dish__name--light { font-weight: 400; }
  .dish__name-ar {
    display: block; font-family: "Noto Kufi Arabic", "Lato", sans-serif;
    font-size: 22px; font-weight: 400; line-height: 34px; direction: rtl;
  }
  .dish__desc {
    max-width: 350px; margin: 28px auto 0; font-size: 17px; line-height: 22px; color: var(--muted);
  }
  .dish__desc--tight { margin-top: 12px; }
  .dish__desc-ar {
    max-width: 360px; margin: 18px auto 0; font-family: "Noto Kufi Arabic", "Lato", sans-serif;
    font-size: 15px; line-height: 22px; color: var(--muted-ar); direction: rtl;
  }
  .price { margin-left: 6px; }
</style>
</head>
<body>
<main class="menu-page">

  <svg class="rules" width="1200" height="2174" viewBox="0 0 1200 2174" aria-hidden="true">
    <g fill="none" stroke="var(--line)" stroke-width="2">
      <line x1="0" y1="123" x2="240" y2="123"/>
      <line x1="942" y1="123" x2="1200" y2="123"/>
      <line x1="667" y1="225" x2="804" y2="225"/>
      <polyline points="378,235 90,235 90,545"/>
      <polyline points="1130,333 1130,572 877,572"/>
      <path d="M58 240 C 80 290, 40 320, 62 370 S 44 450, 66 492"/>
      <line x1="0" y1="887" x2="1200" y2="887"/>
      <polyline points="1130,922 1130,1200 887,1200"/>
      <line x1="0" y1="1504" x2="1200" y2="1504"/>
      <polyline points="1065,1800 1123,1800 1123,2043"/>
      <line x1="0" y1="2084" x2="1200" y2="2084"/>
    </g>
    <g fill="var(--board)" stroke="var(--line)" stroke-width="2">
      <rect x="500" y="871" width="225" height="32" rx="16"/>
      <rect x="482" y="2068" width="235" height="32" rx="16"/>
    </g>
  </svg>

  <h1 class="heading heading--left">MAIN</h1>
  <h1 class="heading heading--right">COURSE</h1>

  <div class="doodle-row" style="left:536px;top:74px;width:131px;height:80px;border-radius:60px 60px 8px 8px" role="img" aria-label="Line drawing of a serving cloche"></div>
  <div class="doodle-row" style="left:239px;top:145px;width:174px;height:56px" role="img" aria-label="Line drawings of a tomato, beetroot and pepper"></div>
  <div class="doodle-row" style="left:782px;top:145px;width:221px;height:56px" role="img" aria-label="Line drawings of cheese and mushrooms"></div>

  <div class="doodle" style="left:566px;top:282px;width:56px;height:56px" role="img" aria-label="Line drawing of a lemon slice"></div>
  <div class="doodle" style="left:566px;top:421px;width:56px;height:56px" role="img" aria-label="Line drawing of an onion"></div>
  <div class="doodle" style="left:566px;top:560px;width:56px;height:56px" role="img" aria-label="Line drawing of a tomato"></div>
  <div class="doodle" style="left:556px;top:706px;width:72px;height:56px" role="img" aria-label="Line drawing of an eggplant"></div>
  <div class="doodle" style="left:576px;top:1040px;width:80px;height:110px" role="img" aria-label="Line drawing of mushrooms"></div>
  <div class="doodle" style="left:566px;top:1186px;width:64px;height:64px" role="img" aria-label="Line drawing of a carrot"></div>
  <div class="doodle" style="left:566px;top:1296px;width:80px;height:80px" role="img" aria-label="Line drawing of beetroots"></div>
  <div class="doodle" style="left:574px;top:1474px;width:48px;height:56px" role="img" aria-label="Line drawing of a pear"></div>
  <div class="doodle" style="left:610px;top:1614px;width:64px;height:64px" role="img" aria-label="Line drawing of an apple"></div>
  <div class="doodle" style="left:578px;top:1768px;width:44px;height:56px" role="img" aria-label="Line drawing of a small fruit"></div>

  <div class="photo photo--left" role="img" aria-label="Photo of grilled chicken breasts with french fries and green beans on an oval plate"></div>
  <div class="photo photo--right" role="img" aria-label="Photo of breaded chicken milanese with creamy spaghetti and green beans"></div>

  <article class="dish dish--left" style="top:578px">
    <h2 class="dish__name">Grilled Chicken with Mushroom Sauce | <span class="dish__name-ar">دجاج مشوي مع صوص الفطر</span></h2>
    <p class="dish__desc">Grilled chicken breasts served with creamy spinach sauce and a side of french fries and green beans<span class="price">55</span></p>
    <p class="dish__desc-ar">فيليه صدور الدجاج المشوية مقدمة مع صوص كريمة السبانخ و البطاطس المقلية و الفاصوليا الخضراء <span>55</span></p>
  </article>

  <article class="dish dish--right" style="top:578px">
    <h2 class="dish__name">Chicken Milanese | <span class="dish__name-ar">دجاج ميلانيز</span></h2>
    <p class="dish__desc">Fried breaded chicken breasts served with spaghetti with cream sauce and a side of green beans<span class="price">55</span></p>
    <p class="dish__desc-ar">فيليه صدور الدجاج المغطاة بالبقسماط، مقلية و مقدمة مع سباجيتي بالكريمة و الفاصوليا الخضراء <span>55</span></p>
  </article>

  <article class="dish dish--left" style="top:914px">
    <h2 class="dish__name">Beef Stroganoff | <span class="dish__name-ar">لحم ستروغونوف</span></h2>
    <p class="dish__desc">Thinly sliced beef cooked with creamy stroganoff sauce &amp; mushrooms, served with white rice<span class="price">55</span></p>
    <p class="dish__desc-ar">شرائح اللحم البقري الخفيفة مع صوص كريمة الستروغونوف و الفطر، مقدمة مع الأرز الأبيض <span>55</span></p>
  </article>

  <article class="dish dish--right" style="top:914px">
    <h2 class="dish__name dish__name--light">Steak with<br>Mushroom Sauce<span class="dish__name-ar">ستيك مع صوص الفطر |</span></h2>
    <p class="dish__desc dish__desc--tight">Grilled filliet mignion topped with creamy green herbs sauce, served with a side of french fries and green beans<span class="price">65</span></p>
    <p class="dish__desc-ar">شرائح لحم الفيليه المشوية، مقدمة مع صوص الكريمة و الفطر و البطاطس المقلية و الفاصوليا الخضراء <span>65</span></p>
  </article>

  <article class="dish dish--left" style="top:1212px">
    <h2 class="dish__name">Shrimp Scampi Bake | <span class="dish__name-ar">جمبري سكامبي بالفرن</span></h2>
    <p class="dish__desc">Shrimps baked with mashed potatos, bechamel sauce, and mozzarella cheese. Served with spaghetti pasta and green beans<span class="price">55</span></p>
    <p class="dish__desc-ar">طاجن الجمبري و البطاطس المهروسة، مخبوز في الفرن مع البشاميل و الجبنة، و يقدم مع معكرونة السباجيتي و الفاصوليا الخضراء <span>55</span></p>
  </article>

  <article class="dish dish--right" style="top:1212px">
    <h2 class="dish__name">Grilled Chicken<br>with Spinach<br>Sauce | <span class="dish__name-ar">دجاج مشوي مع صوص</span></h2>
    <p class="dish__desc dish__desc--tight">Grilled chicken breasts served with creamy spinach sauce and a side of french fries and green beans<span class="price">55</span></p>
    <p class="dish__desc-ar" style="margin-top:8px">فيليه صدور الدجاج المشوية مقدمة مع صوص كريمة السبانخ و البطاطس المقلية و الفاصوليا الخضراء <span>55</span></p>
  </article>

  <article class="dish dish--left" style="top:1527px">
    <h2 class="dish__name">Steak with Herb Sauce | <span class="dish__name-ar">ستيك مع صوص الأعشاب</span></h2>
    <p class="dish__desc">Grilled filliet mignion topped with creamy green herbs sauce, served with a side of french fries and green beans<span class="price">65</span></p>
    <p class="dish__desc-ar">شرائح لحم الفيليه المشوية، مقدمة مع صوص الكريمة و الأعشاب و البطاطس المقلية و الفاصوليا الخضراء <span>65</span></p>
  </article>

  <article class="dish dish--right" style="top:1527px">
    <h2 class="dish__name">Chicken Parmigiana | <span class="dish__name-ar">دجاج بارميجيانا</span></h2>
    <p class="dish__desc">Fried breaded chicken breasts topped with melted parmesan &amp; mozzarella cheese &amp; marinara sauce. Served with spaghetti pasta<span class="price">55</span></p>
    <p class="dish__desc-ar">فيليه صدور الدجاج المقلية بالبقسماط، مغطاة بجبنة البارميجيان و الموزاريلا الذائبة و صوص المارينارا و مقدمة مع معكرونة السباجيتي <span>55</span></p>
  </article>

  <article class="dish dish--left" style="top:1824px">
    <h2 class="dish__name">Steak Beijing | <span class="dish__name-ar">ستيك بيجينج</span></h2>
    <p class="dish__desc dish__desc--tight">Grilled filliet mignion covered with a sweet and tangy soy glaze served with french fries and broccoli<span class="price">65</span></p>
    <p class="dish__desc-ar">شرائح لحم الفيليه المشوية، مغطاة بصوص الصويا الحلو و الحامض و مقدمة مع البطاطس المقلية و البروكلي <span>65</span></p>
  </article>

  <article class="dish dish--right" style="top:1824px">
    <h2 class="dish__name">Shrimp &amp; Mash | <span class="dish__name-ar">شرمب اند ماش</span></h2>
    <p class="dish__desc dish__desc--tight">Grilled shrimps served on a bed of mashed potatoes and topped with creamy mushroom sauce. Served with a side of green beans<span class="price">69</span></p>
    <p class="dish__desc-ar">جمبري مشوي مقدم على البطاطس المهروسة و مغطى بصوص الكريمة و الفطر و يقدم مع الفاصوليا الخضراء <span>69</span></p>
  </article>

</main>
</body>
</html>
```